Meadowlark Property Review is a leading provider of residential appraisal and home inspection products in S

I need a business card/logo designed that obviously describes my business. We are a residential appraisal and home inspection company in Springfield, MO. We offer residential appraisals, home inspection, pest inspection and radon gas measurement. We have been in business for 18 years and hold state certified residential appraisal licenses and OBREX certified home inspection licenses. I have a logo that I really like and will attach, but would be open to new suggestions. I like more modern designs than traditional and would like a two sided card with our services, licenses and qualifications on the back.

```html
<!DOCTYPE html>
<html lang="en">
<head>
<meta charset="utf-8">
<title>Meadowlark Property Review – Business Card</title>
<link rel="stylesheet" href="https://fonts.googleapis.com/css2?family=Open+Sans:wght@400;600;700&display=swap">
<style>
  :root {
    --page: #e4e4e4;
    --card-light: #f4f4f4;
    --card-shade: #d9d9d9;
    --brown: #573a1a;
    --brown-mid: #8a6a45;
    --orange: #ef8c1f;
    --ink: #1c1c1c;
    --white: #ffffff;
  }
  * { margin: 0; padding: 0; box-sizing: border-box; }
  html, body {
    width: 1189px; height: 1200px; overflow: hidden;
    background: var(--page);
    font-family: "Open Sans", Arial, sans-serif;
  }
  .card {
    position: absolute; left: 140px; width: 917px; height: 523px;
    background: radial-gradient(ellipse at 50% 30%, var(--card-light) 0%, var(--card-shade) 100%);
    overflow: hidden;
  }
  .card--front { top: 46px; }
  .card--back { top: 623px; }

  .brand-name {
    position: absolute; left: 0; right: 0;
    text-align: center; font-weight: 700; font-size: 40px;
    color: var(--brown); letter-spacing: 0.5px;
  }
  .card--front .brand-name { top: 150px; }
  .card--back .brand-name { top: 165px; }

  .front-wave { position: absolute; inset: 0; width: 100%; height: 100%; }

  .phones {
    position: absolute; top: 352px; left: 60px; width: 254px;
    color: var(--white); font-size: 28px; line-height: 32px;
  }
  .phones li { list-style: none; display: flex; justify-content: flex-end; align-items: center; gap: 18px; }
  .icon { width: 20px; height: 20px; flex: none; }

  .divider {
    position: absolute; left: 344px; top: 287px; width: 4px; height: 204px;
    background: var(--white);
  }

  .contact {
    position: absolute; top: 352px; left: 384px;
    color: var(--white); font-size: 28px; line-height: 32px;
  }
  .contact li { list-style: none; display: flex; align-items: center; gap: 15px; }
  .contact li.cont { padding-left: 35px; }

  .services {
    position: absolute; top: 266px; display: flex; flex-direction: column;
    font-size: 27px; line-height: 32px; color: var(--ink);
  }
  .services--left { left: 72px; }
  .services--right { left: 519px; top: 260px; }
  .services li { list-style: none; display: flex; align-items: center; gap: 10px; }
  .tick { width: 24px; height: 24px; flex: none; margin-top: 6px; }
</style>
</head>
<body>

<section class="card card--front">
  <svg class="front-wave" viewBox="0 0 1123 641" preserveAspectRatio="none" aria-hidden="true">
    <path d="M0 325 C 250 350, 420 340, 620 300 C 820 255, 960 245, 1123 320 L1123 641 L0 641 Z" fill="var(--brown)"/>
  </svg>
  <div class="brand-name">Meadowlark Property Review</div>

  <ul class="phones">
    <li>417-555-0142
      <svg class="icon" viewBox="0 0 20 20"><rect width="20" height="20" fill="var(--white)"/><rect x="6" y="3" width="8" height="14" rx="1" fill="var(--brown)"/><rect x="7.5" y="5" width="5" height="4" fill="var(--white)"/></svg>
    </li>
    <li>417-555-0187
      <svg class="icon" viewBox="0 0 20 20"><rect width="20" height="20" fill="var(--white)"/><path d="M6 3 L9 4 L8.5 7.5 L7.5 8 C8 10.5 9.5 12 12 12.5 L12.5 11.5 L16 11 L17 14 C15 17 11 16.5 8 13.5 C5 10.5 4 6 6 3 Z" fill="var(--brown)"/></svg>
    </li>
    <li>417-555-0139
      <svg class="icon" viewBox="0 0 20 20"><rect width="20" height="20" fill="var(--white)"/><rect x="6" y="3" width="8" height="4" fill="var(--brown)"/><rect x="3" y="7" width="14" height="7" fill="var(--brown)"/><rect x="6" y="12" width="8" height="5" fill="var(--brown)" stroke="var(--white)" stroke-width="1"/></svg>
    </li>
  </ul>

  <div class="divider"></div>

  <ul class="contact">
    <li>
      <svg class="icon" viewBox="0 0 20 20"><rect width="20" height="20" fill="var(--white)"/><rect x="3" y="5" width="14" height="10" fill="var(--brown)"/><path d="M3.5 5.5 L10 11 L16.5 5.5" stroke="var(--white)" stroke-width="1.2" fill="none"/></svg>
      info@meadowlarkreview.com
    </li>
    <li>
      <svg class="icon" viewBox="0 0 20 20"><rect width="20" height="20" fill="var(--white)"/><path d="M10 17 C7 12.5 5.5 10.5 5.5 8 A4.5 4.5 0 0 1 14.5 8 C14.5 10.5 13 12.5 10 17 Z" fill="var(--brown)"/><circle cx="10" cy="8" r="1.7" fill="var(--white)"/></svg>
      Meadowlark Property Review
    </li>
    <li class="cont">4410 S Fremont Avenue; Suite C</li>
    <li class="cont">Springfield, MO&nbsp; 65810</li>
  </ul>
</section>

<section class="card card--back">
  <div class="brand-name">Meadowlark Property Review</div>

  <ul class="services services--left">
    <li><svg class="tick" viewBox="0 0 24 24"><path d="M2 13 L7 11 L10 17 C13 10 17 5 23 2 C17 7 13 14 10 22 Z" fill="var(--brown-mid)"/></svg>home inspection</li>
    <li><svg class="tick" viewBox="0 0 24 24"><path d="M2 13 L7 11 L10 17 C13 10 17 5 23 2 C17 7 13 14 10 22 Z" fill="var(--brown-mid)"/></svg>property inspection</li>
    <li><svg class="tick" viewBox="0 0 24 24"><path d="M2 13 L7 11 L10 17 C13 10 17 5 23 2 C17 7 13 14 10 22 Z" fill="var(--brown-mid)"/></svg>residential appraisal</li>
    <li><svg class="tick" viewBox="0 0 24 24"><path d="M2 13 L7 11 L10 17 C13 10 17 5 23 2 C17 7 13 14 10 22 Z" fill="var(--brown-mid)"/></svg>termite inspection</li>
    <li><svg class="tick" viewBox="0 0 24 24"><path d="M2 13 L7 11 L10 17 C13 10 17 5 23 2 C17 7 13 14 10 22 Z" fill="var(--brown-mid)"/></svg>radon gas measurement</li>
    <li><svg class="tick" viewBox="0 0 24 24"><path d="M2 13 L7 11 L10 17 C13 10 17 5 23 2 C17 7 13 14 10 22 Z" fill="var(--brown-mid)"/></svg>pre purchase inspection</li>
  </ul>

  <ul class="services services--right">
    <li><svg class="tick" viewBox="0 0 24 24"><path d="M2 13 L7 11 L10 17 C13 10 17 5 23 2 C17 7 13 14 10 22 Z" fill="var(--brown-mid)"/></svg>thermal imaging</li>
    <li><svg class="tick" viewBox="0 0 24 24"><path d="M2 13 L7 11 L10 17 C13 10 17 5 23 2 C17 7 13 14 10 22 Z" fill="var(--brown-mid)"/></svg>mechanical inspection</li>
    <li><svg class="tick" viewBox="0 0 24 24"><path d="M2 13 L7 11 L10 17 C13 10 17 5 23 2 C17 7 13 14 10 22 Z" fill="var(--brown-mid)"/></svg>tax appeal</li>
    <li><svg class="tick" viewBox="0 0 24 24"><path d="M2 13 L7 11 L10 17 C13 10 17 5 23 2 C17 7 13 14 10 22 Z" fill="var(--brown-mid)"/></svg>asset evaluation</li>
    <li><svg class="tick" viewBox="0 0 24 24"><path d="M2 13 L7 11 L10 17 C13 10 17 5 23 2 C17 7 13 14 10 22 Z" fill="var(--brown-mid)"/></svg>energy audits</li>
  </ul>
</section>

</body>
</html>
```